eBook cover and content: Steering Teams With Quiet Courage

I teach a leadership program to companies that was developed at Varnelo and now need an eBook cover and content design. This downloadable eBook will be offered online in exchange for prospects' contact details. It needs to be designed with a sophisticated, senior HR executive audience in mind. There are some assets that are available for you to work with including photographs, a logo device for the program, and a colour palette (same as Varnelo's blue, green, yellow and red). Note that while the program was developed at Varnelo it is NOT a Varnelo product and I need to ensure that the eBook does not breach license guidelines. I have attached a very rough mockup of the content, images and graphic elements to help.

Target Market(s)

Senior business leaders and HR professionals.

Industry/Entity Type

Leadership

Font styles to use
Sans Serif

Requirements
Must have
• Keep it simple. Clean, contemporary, professional feel. This is a high-value decision for a company and needs to look modern, progressive and credible. Downloadable PDF. Easy to read and digest layout.
• Colours - see attached screenshot for red, blue, green, yellow ref. Additionally charcoal for most type and purple 330033 as extra colour is okay.
• Landscape format please.
Nice to have
• Plenty of white space.

```html
<!DOCTYPE html>
<html lang="en">
<head>
<meta charset="utf-8">
<title>Steering Teams With Quiet Courage – About the Teacher</title>
<link rel="stylesheet" href="https://fonts.googleapis.com/css2?family=Raleway:wght@300;400&family=Roboto:wght@400&display=swap">
<style>
  :root {
    --backdrop: #f0f0f0;
    --paper: #ffffff;
    --brand-blue: #4a72c0;
    --charcoal: #4a4a4a;
    --ink: #222222;
    --muted: #777777;
    --accent-red: #d9352b;
  }
  * { margin: 0; padding: 0; box-sizing: border-box; }
  html, body { width: 1200px; height: 851px; overflow: hidden; }
  body { background: var(--backdrop); position: relative; font-family: "Raleway", sans-serif; }

  .page {
    position: absolute; left: 16px; width: 568px; height: 395px;
    background: var(--paper);
    box-shadow: 0 2px 4px rgba(0,0,0,0.18);
  }
  .page--about { top: 22px; }
  .page--closing { top: 435px; }

  .running-brand {
    position: absolute; left: 20px; top: 20px;
    display: flex; align-items: center; gap: 5px;
    font-family: "Roboto", sans-serif; font-size: 7px; color: var(--ink);
  }
  .brand-dot { width: 7px; height: 7px; border-radius: 50%; background: var(--brand-blue); }

  .about-title {
    position: absolute; left: 19px; top: 58px;
    font-weight: 300; font-size: 20px; line-height: 21px;
    color: var(--brand-blue); letter-spacing: 0.2px;
  }
  .about-rule {
    position: absolute; left: 19px; top: 107px;
    width: 60px; height: 3px; background: var(--brand-blue);
  }

  .bio {
    position: absolute; left: 199px; top: 61px; width: 345px;
    font-size: 7.6px; line-height: 10.3px; color: var(--charcoal);
  }
  .bio p + p { margin-top: 6px; }

  .folio {
    position: absolute; right: 17px; bottom: 11px;
    font-size: 7px; color: var(--brand-blue);
  }
  .folio-tab {
    position: absolute; right: 0; bottom: 10px;
    width: 6px; height: 12px; background: var(--brand-blue);
  }

  .signoff {
    position: absolute; left: 210px; top: 166px;
    display: flex; align-items: center; gap: 10px;
  }
  .signoff .brand-dot { width: 22px; height: 22px; }
  .signoff-name { font-family: "Roboto", sans-serif; font-size: 10.5px; color: var(--ink); line-height: 13px; }
  .signoff-role { font-family: "Roboto", sans-serif; font-size: 10.5px; color: var(--muted); line-height: 13px; }

  .contact-email {
    position: absolute; left: 237px; top: 336px;
    font-size: 9px; color: var(--accent-red);
  }
</style>
</head>
<body>
  <section class="page page--about">
    <div class="running-brand"><span class="brand-dot"></span>Quiet Courage</div>
    <h1 class="about-title">ABOUT<br>OWEN MARSH</h1>
    <div class="about-rule"></div>
    <div class="bio">
      <p>Owen is a QC Certified Teacher, a serial entrepreneur, advisor, Board member and Adjunct Professor at Harbourline Business School. He is one of the world's most accomplished advertis-ing and marketing experts having lived and worked around the world for 10 years before returning home to Australia.</p>
      <p>He's created award-winning campaigns for Brightvale Home, Fizzmont, Korimo Motors, Sonata Electronics, Crestbridge Bank, Alpenmilk, Fordham Auto, Paylark, Unimora, Coralfuel, Hartley &amp; Hale, Distillia, Eastgate Bank, Bergmann Pharma, Harbour Light and Power, Netvista, RMTA, and many others.</p>
      <p>Owen has also led business and cultural transformations across international networks of 11,000 people. Twice.</p>
      <p>He is Co-Founder of Parcelo, a technology company taking on Coastpost in the parcel delivery market. Parcelo has been recognised as one of Australia's Top 10 Most Innovative Companies, two years running. The company now has tens of thousands of customers and has grown at an average of 15% per month since launch 4 years ago.</p>
      <p>Owen is passionate about helping people build the skills for sustained high- performance and has taught QC across Australia, NZ and Asia to startups, government organisations and global companies.</p>
      <p>He also happens to be the fastest Australian to run a marathon at the North Pole.</p>
    </div>
    <span class="folio">15</span>
    <span class="folio-tab"></span>
  </section>

  <section class="page page--closing">
    <div class="signoff">
      <span class="brand-dot"></span>
      <div>
        <div class="signoff-name">Quiet Courage</div>
        <div class="signoff-role">Certified Teacher</div>
      </div>
    </div>
    <p class="contact-email">qc@owenmarshnow.com</p>
  </section>
</body>
</html>
```